Corporate Business Card

Very professional, Modern, Not to busy, include phone address email, website
(253) 617-4930, 18761 52nd Avenue S, Kent, WA 98047, martin@plumlinegroup.com, varkoworks.com

Target Market(s)

Manufacturing

Industry/Entity Type

Aero, machining, manufacturing, Off road racing

Contact Information for Business Card

Phone, address email, website

```html
<!DOCTYPE html>
<html lang="en">
<head>
<meta charset="utf-8">
<title>Varko Works – Business Card</title>
<link rel="stylesheet" href="https://fonts.googleapis.com/css2?family=Arimo:wght@400;700&display=swap">
<style>
  :root {
    --navy: #13306a;
    --navy-deep: #0f2858;
    --navy-faint: #1a3a78;
    --red: #d8232f;
    --white: #f6f6f6;
    --stage: #2a2b2e;
    --text-light: #ffffff;
  }
  * { box-sizing: border-box; margin: 0; padding: 0; }
  html, body {
    width: 1200px; height: 874px; overflow: hidden;
    background: var(--stage);
    font-family: "Arimo", Arial, sans-serif;
  }
  .canvas {
    position: relative; width: 1200px; height: 874px;
  }
  .card {
    position: absolute; left: 290px; width: 620px; height: 354px;
    box-shadow: 0 10px 26px rgba(0,0,0,.45);
    overflow: hidden;
  }
  .card--back { top: 60px; background: var(--navy); }
  .card--front { top: 460px; background: var(--white); }

  .back-name {
    position: absolute; inset: 0;
    display: flex; align-items: center; justify-content: center;
    font-size: 64px; font-weight: 700; letter-spacing: 2px;
    color: var(--navy-faint);
  }

  .brand {
    position: absolute; left: 40px; top: 0; width: 270px; height: 354px;
    display: flex; align-items: center; justify-content: center;
    font-size: 38px; font-weight: 700; color: var(--navy);
    letter-spacing: 1px;
  }

  .accent-bar {
    position: absolute; left: 330px; top: 62px; width: 7px; height: 232px;
    background: var(--red);
  }
  .contact-panel {
    position: absolute; left: 343px; right: 0; top: 62px; height: 232px;
    background: var(--navy); color: var(--text-light);
    padding: 24px 20px 0 30px;
  }
  .person-name { font-size: 22px; font-weight: 700; letter-spacing: .5px; }
  .person-role { font-size: 13px; margin-top: 3px; }
  .address { font-size: 15px; line-height: 19px; margin-top: 14px; }
  .contact-list { list-style: none; margin-top: 12px; font-size: 15px; line-height: 20px; }
  .contact-list li { display: flex; align-items: center; gap: 9px; }
  .contact-list svg { width: 12px; height: 12px; fill: var(--text-light); flex: none; }
</style>
</head>
<body>
<main class="canvas">
  <section class="card card--back" aria-label="Card back">
    <div class="back-name">Varko Works</div>
  </section>

  <section class="card card--front" aria-label="Card front">
    <div class="brand">Varko Works</div>
    <div class="accent-bar"></div>
    <div class="contact-panel">
      <h1 class="person-name">DANIEL BROOKS</h1>
      <p class="person-role">Managing Director</p>
      <p class="address">18761 52nd Avenue S<br>Kent, WA 98047</p>
      <ul class="contact-list">
        <li>
          <svg viewBox="0 0 24 24" aria-hidden="true"><path d="M6.6 10.8a15.1 15.1 0 0 0 6.6 6.6l2.2-2.2a1 1 0 0 1 1-.25 11.4 11.4 0 0 0 3.6.57 1 1 0 0 1 1 1V20a1 1 0 0 1-1 1A17 17 0 0 1 3 4a1 1 0 0 1 1-1h3.5a1 1 0 0 1 1 1c0 1.25.2 2.45.57 3.57a1 1 0 0 1-.25 1z"/></svg>
          (253) 617-4930
        </li>
        <li>
          <svg viewBox="0 0 24 24" aria-hidden="true"><path d="M2 5h20v14H2z M3.5 6.5 12 13l8.5-6.5" fill="none" stroke="#fff" stroke-width="2"/></svg>
          martin@plumlinegroup.com
        </li>
        <li>
          <svg viewBox="0 0 24 24" aria-hidden="true"><circle cx="12" cy="12" r="10"/></svg>
          varkoworks.com
        </li>
      </ul>
    </div>
  </section>
</main>
</body>
</html>
```